Residential Remodeling Contractor needs updated business card

I need a new design for my business card.
Name of the company is Ridgefell Construction. I need a card that commands presence, strength, integrity. I have been in business for 28 years. I am a Residential Remodeling Contractor that covers all aspects of a residential remodel and build.

```html
<!DOCTYPE html>
<html lang="en">
<head>
<meta charset="UTF-8">
<title>Ridgefell Construction – Business Card</title>
<link href="https://fonts.googleapis.com/css2?family=Cinzel:wght@700&family=Poppins:ital,wght@0,400;0,500;1,400&display=swap" rel="stylesheet">
<style>
  :root {
    --navy: #1f3d7e;
    --navy-soft: #33579f;
    --ink: #2b2b2b;
    --paper: #ffffff;
    --backdrop: #9b9b9b;
  }
  * { margin: 0; padding: 0; box-sizing: border-box; }
  html, body {
    width: 1093px; height: 1200px; overflow: hidden;
    background: var(--backdrop);
    font-family: "Poppins", sans-serif;
  }
  .canvas { position: relative; width: 1093px; height: 1200px; }

  .card {
    position: absolute; left: 265px;
    width: 578px; height: 356px;
    border-radius: 24px; overflow: hidden;
  }
  .card-front { top: 226px; background: var(--paper); }
  .card-back  { top: 621px; background: var(--navy); width: 582px; height: 357px; }

  .holder { position: absolute; left: 26px; top: 50px; }
  .holder-name {
    font-family: "Cinzel", serif; font-weight: 700;
    font-size: 22px; line-height: 1; color: var(--navy); letter-spacing: 0.2px;
  }
  .holder-title { font-size: 16px; line-height: 1.1; color: var(--ink); margin-top: 1px; }

  .brand {
    position: absolute; right: 27px; top: 62px;
    text-align: right; color: var(--navy);
    font-family: "Cinzel", serif; font-weight: 700; line-height: 1.1;
  }
  .brand-line1 { font-size: 32px; }
  .brand-line2 { font-size: 22px; }

  .contacts { position: absolute; left: 26px; top: 214px; list-style: none; }
  .contacts li {
    display: flex; align-items: center; gap: 7px;
    font-size: 16.5px; line-height: 21px; color: var(--ink);
  }
  .contacts svg { width: 16px; height: 16px; flex: none; fill: var(--navy); }
  .contacts .accent { color: var(--navy); }

  .address {
    position: absolute; right: 27px; top: 236px;
    text-align: right; font-size: 16.5px; line-height: 21px; color: var(--ink);
  }

  .tagline-band {
    position: absolute; left: 0; right: 0; bottom: 0; height: 63px;
    background: var(--navy); color: var(--paper);
    text-align: center; padding-top: 6px;
  }
  .tagline-since { font-style: italic; font-size: 16.5px; line-height: 20px; }
  .tagline-service { font-weight: 500; font-size: 15.5px; line-height: 22px; letter-spacing: 0.2px; }

  .back-brand {
    position: absolute; left: 0; right: 0; top: 132px;
    text-align: center; color: var(--navy-soft);
    font-family: "Cinzel", serif; font-weight: 700; line-height: 1.05;
  }
  .back-brand .brand-line1 { font-size: 50px; }
  .back-brand .brand-line2 { font-size: 34px; }
</style>
</head>
<body>
<main class="canvas">

  <section class="card card-front" aria-label="Business card front">
    <div class="holder">
      <p class="holder-name">DANIEL HARTWELL</p>
      <p class="holder-title">Managing Director</p>
    </div>

    <div class="brand">
      <p class="brand-line1">RIDGEFELL</p>
      <p class="brand-line2">CONSTRUCTION</p>
    </div>

    <ul class="contacts">
      <li>
        <svg viewBox="0 0 24 24" aria-hidden="true"><path d="M6.6 10.8a15.1 15.1 0 0 0 6.6 6.6l2.2-2.2a1 1 0 0 1 1-.25 11.4 11.4 0 0 0 3.6.57 1 1 0 0 1 1 1V20a1 1 0 0 1-1 1A17 17 0 0 1 3 4a1 1 0 0 1 1-1h3.5a1 1 0 0 1 1 1c0 1.25.2 2.45.57 3.6a1 1 0 0 1-.25 1z"/></svg>
        044-555 018 273
      </li>
      <li>
        <svg viewBox="0 0 24 24" aria-hidden="true"><path d="M2 5h20v14H2zm2 2v.5l8 5.5 8-5.5V7zm0 3v7h16v-7l-8 5.5z"/></svg>
        info@ridgefellbuild.com
      </li>
      <li>
        <svg viewBox="0 0 24 24" aria-hidden="true"><path d="M12 2a10 10 0 1 0 0 20 10 10 0 0 0 0-20zm6.9 9h-3a15 15 0 0 0-1.3-6A8 8 0 0 1 18.9 11zM12 4c.9 1.2 1.7 3.7 1.9 7h-3.8c.2-3.3 1-5.8 1.9-7zM9.4 5a15 15 0 0 0-1.3 6h-3A8 8 0 0 1 9.4 5zM5.1 13h3a15 15 0 0 0 1.3 6A8 8 0 0 1 5.1 13zM12 20c-.9-1.2-1.7-3.7-1.9-7h3.8c-.2 3.3-1 5.8-1.9 7zm2.6-1a15 15 0 0 0 1.3-6h3a8 8 0 0 1-4.3 6z"/></svg>
        <span>www.<span class="accent">ridgefellbuild</span>.com</span>
      </li>
    </ul>

    <address class="address" style="font-style: normal;">
      421, Alder Brook Road<br>
      45452, Westmere
    </address>

    <div class="tagline-band">
      <p class="tagline-since">Since 28 years</p>
      <p class="tagline-service">RESIDENTIAL CONTRACTOR FOR REMODELING AND BUILD</p>
    </div>
  </section>

  <section class="card card-back" aria-label="Business card back">
    <div class="back-brand">
      <p class="brand-line1">RIDGEFELL</p>
      <p class="brand-line2">CONSTRUCTION</p>
    </div>
  </section>

</main>
</body>
</html>
```